Brell Stone Company Business Cards

Front and Back Business Card - logo and text setup - cool design. I need workable photoshop or illustrator files so I can setup each employee card with design that is created
Updates

Hi everyone, thank you for the great entries. Please no more white and blue cards - there are so many already - black and silver only now please. thanks!

Target Market(s)

Construction Industry - Facility Managers

Industry/Entity Type

Construction

Contact Information for Business Card

I really like contemporary simplistic looks - clean neat....not opposed to seeing some black backrounds

Requirements
Must have
• Logo/website address with design on front only - www.brellstone-example.com (logo attached)
• Back:
• Name/Title/Company Address/Phone/email address
Nice to have
• Cool design
Should not have
• Nothing gimmicky like Fire or Water - since we are a Fire Protection company - it has all been done

```html
<!DOCTYPE html>
<html lang="en">
<head>
<meta charset="utf-8">
<title>Brell Stone Company Business Cards</title>
<link href="https://fonts.googleapis.com/css2?family=Lato:wght@400;700;900&display=swap" rel="stylesheet">
<style>
  :root {
    --black: #161616;
    --silver: #c4c6c9;
    --silver-light: #e2e4e6;
    --silver-dark: #9fa2a6;
    --ink-soft: #b3b5b8;
    --rule: #55585c;
    --backdrop: #e9e9e9;
  }
  html, body {
    margin: 0;
    width: 1200px;
    height: 1200px;
    overflow: hidden;
    background: var(--backdrop);
    font-family: "Lato", sans-serif;
  }
  .canvas { position: relative; width: 1200px; height: 1200px; }
  .card {
    position: absolute;
    top: 310px;
    width: 364px;
    height: 594px;
    box-shadow: 2px 3px 6px rgba(0,0,0,.25);
  }
  .card--front { left: 234px; background: var(--black); }
  .card--back {
    left: 627px;
    width: 369px;
    background: linear-gradient(135deg, var(--silver-light) 0%, var(--silver) 50%, var(--silver-dark) 100%);
  }
  .wordmark {
    position: absolute;
    left: 0; right: 0;
    text-align: center;
    font-weight: 900;
    font-size: 56px;
    letter-spacing: -1px;
    line-height: 1;
  }
  .card--front .wordmark { top: 140px; color: var(--silver); }
  .card--back .wordmark { top: 262px; color: var(--black); }
  .person {
    position: absolute;
    top: 334px; left: 0; right: 0;
    text-align: center;
  }
  .person__name {
    margin: 0;
    font-size: 22px;
    font-weight: 400;
    color: var(--silver-light);
    line-height: 1.2;
  }
  .person__name .surname { font-weight: 700; color: var(--silver-light); }
  .person__title { margin: 2px 0 0; font-size: 17px; color: var(--ink-soft); }
  .contact-icons { position: absolute; top: 395px; left: 87px; }
  .contact-list, .address {
    position: absolute; left: 0; right: 0;
    margin: 0; text-align: center;
    font-size: 17px; line-height: 22px; color: var(--ink-soft);
    font-style: normal;
  }
  .contact-list { top: 431px; list-style: none; padding: 0; }
  .divider {
    position: absolute; top: 507px; left: 88px; width: 195px;
    height: 1px; background: var(--rule);
  }
  .address { top: 518px; }
  .back-url {
    position: absolute; top: 531px; left: 0; right: 0;
    text-align: center; font-size: 17px; color: var(--black);
  }
</style>
</head>
<body>
<main class="canvas">
  <section class="card card--front" aria-label="Card front">
    <div class="wordmark">Brell Stone</div>
    <div class="person">
      <h1 class="person__name">DANIEL <span class="surname">HART</span></h1>
      <p class="person__title">Managing Director</p>
    </div>
    <svg class="contact-icons" width="190" height="26" viewBox="0 0 190 26" aria-hidden="true">
      <line x1="0" y1="13" x2="54" y2="13" stroke="#6a6d71" stroke-width="1"/>
      <line x1="136" y1="13" x2="190" y2="13" stroke="#6a6d71" stroke-width="1"/>
      <circle cx="67" cy="13" r="12" fill="#c4c6c9"/>
      <circle cx="95" cy="13" r="12" fill="#c4c6c9"/>
      <circle cx="122" cy="13" r="12" fill="#c4c6c9"/>
      <path d="M60 11 q7-6 14 0 l-2 2 -2-1 v-1 h-6 v1 l-2 1z M62 14 h10 v5 h-10z" fill="#161616"/>
      <rect x="88" y="8" width="14" height="10" fill="none" stroke="#161616" stroke-width="1.4"/>
      <path d="M88 8 l7 6 7-6" fill="none" stroke="#161616" stroke-width="1.4"/>
      <circle cx="122" cy="13" r="6.5" fill="none" stroke="#161616" stroke-width="1.4"/>
      <path d="M115.5 13 h13 M122 6.5 q-4 6.5 0 13 M122 6.5 q4 6.5 0 13" fill="none" stroke="#161616" stroke-width="1"/>
    </svg>
    <ul class="contact-list">
      <li>044-555 010 234</li>
      <li>info@brellstone-example.com</li>
      <li>www.brellstone-example.com</li>
    </ul>
    <div class="divider"></div>
    <address class="address">421, Address line here,<br>45452,Country Name</address>
  </section>

  <section class="card card--back" aria-label="Card back">
    <div class="wordmark">Brell Stone</div>
    <div class="back-url">www.brellstone-example.com</div>
  </section>
</main>
</body>
</html>
```